Simple and Clean business card design

We would like the design to be simple clean and to incorporate our colors.

We are open to your design and talent, we have the dots in our logo as we think of it as data points and we connect data points for people.

We are open to see the great creative and clean design you bring to the table

Contact Information for Business Card

please include: name, position, email, phone and website

Font styles to use
Sans Serif

Requirements
Must have
• my colors incorporated, simplicity
Nice to have
• lots of white space, simplicity
Should not have
• complexicity/ complex art

```html
<!DOCTYPE html>
<html lang="en">
<head>
<meta charset="utf-8">
<title>Nectra Business Card</title>
<link rel="stylesheet" href="https://fonts.googleapis.com/css2?family=Open+Sans:wght@400;600&family=Saira:wght@500;600&display=swap">
<style>
  :root {
    --page: #fdfdfd;
    --ink: #000000;
    --text: #222222;
    --paper: #ffffff;
    --brand-blue: #4285f4;
    --rule: #333333;
  }
  * { margin: 0; padding: 0; box-sizing: border-box; }
  html, body { width: 1200px; height: 1200px; overflow: hidden; background: var(--page); }
  .canvas { position: relative; width: 1200px; height: 1200px; }

  .card { position: absolute; left: 215px; width: 771px; height: 429px; overflow: hidden; }
  .card--back {
    top: 146px; background: var(--ink);
    display: flex; align-items: center; justify-content: center;
  }
  .card--front { top: 626px; background: var(--paper); border: 1px solid var(--rule); }

  .wordmark {
    font-family: "Open Sans", sans-serif;
    font-weight: 600;
    letter-spacing: 1px;
    line-height: 1;
    display: flex;
    align-items: center;
    gap: 12px;
    white-space: nowrap;
  }
  .wordmark__dot { border-radius: 50%; flex: none; }

  .card--back .wordmark { font-size: 84px; color: var(--paper); }
  .card--back .wordmark__dot { width: 22px; height: 22px; background: var(--paper); }

  .card--front .wordmark {
    position: absolute; right: 43px; top: 62px;
    font-size: 90px; color: var(--ink);
  }
  .card--front .wordmark__dot { width: 24px; height: 24px; background: var(--brand-blue); }

  .divider {
    position: absolute; left: 40px; top: 203px; width: 606px; height: 1.5px;
    background: linear-gradient(90deg, var(--rule) 0%, var(--rule) 45%, rgba(51,51,51,0) 100%);
  }

  .person { position: absolute; left: 40px; top: 216px; }
  .person__name {
    font-family: "Saira", sans-serif; font-weight: 600; font-size: 39px;
    color: var(--brand-blue); letter-spacing: 1px; line-height: 1.1;
  }
  .person__role {
    font-family: "Saira", sans-serif; font-weight: 500; font-size: 19px;
    color: var(--ink); letter-spacing: 2.5px; line-height: 1.2; margin-top: 2px;
  }

  .contacts { position: absolute; left: 40px; top: 300px; list-style: none; }
  .contacts__item {
    display: flex; align-items: center; height: 33px;
    font-family: "Open Sans", sans-serif; font-size: 21px; color: var(--text);
  }
  .contacts__icon { width: 26px; height: 26px; margin-right: 14px; flex: none; }
</style>
</head>
<body>
<main class="canvas">
  <section class="card card--back">
    <div class="wordmark"><span>Nectra</span><span class="wordmark__dot"></span></div>
  </section>

  <section class="card card--front">
    <div class="wordmark"><span>Nectra</span><span class="wordmark__dot"></span></div>
    <div class="divider"></div>
    <div class="person">
      <h1 class="person__name">MARK ELLIS</h1>
      <p class="person__role">CEO/FOUNDER</p>
    </div>
    <ul class="contacts">
      <li class="contacts__item">
        <svg class="contacts__icon" viewBox="0 0 24 24" aria-hidden="true">
          <path fill="var(--brand-blue)" d="M5 2.5l3 -1 2.5 4.5 -2 1.8c1 2.8 3 5.2 5.8 6.8l1.8 -1.8 4.4 2.6 -1 3c-.5 1-1.6 1.5-2.7 1.2C9.5 17.6 5 12.6 3.8 5.6 3.6 4.2 4 3 5 2.5z"/>
        </svg>
        <span>555-318-0147</span>
      </li>
      <li class="contacts__item">
        <svg class="contacts__icon" viewBox="0 0 24 24" aria-hidden="true" fill="none" stroke="var(--brand-blue)" stroke-width="1.3">
          <circle cx="12" cy="12" r="10.5"/>
          <ellipse cx="12" cy="12" rx="4.5" ry="10.5"/>
          <line x1="12" y1="1.5" x2="12" y2="22.5"/>
          <line x1="1.5" y1="12" x2="22.5" y2="12"/>
          <path d="M3.5 6.5h17M3.5 17.5h17"/>
        </svg>
        <span>www.nectra.one</span>
      </li>
      <li class="contacts__item">
        <svg class="contacts__icon" viewBox="0 0 24 24" aria-hidden="true">
          <rect x="1" y="5" width="22" height="15" fill="var(--brand-blue)"/>
          <path d="M1.5 5.5L12 14 22.5 5.5M1.5 19.5l8 -7M22.5 19.5l-8 -7" fill="none" stroke="#ffffff" stroke-width="1.2"/>
        </svg>
        <span>mark.ellis@nectra.one</span>
      </li>
    </ul>
  </section>
</main>
</body>
</html>
```